Corvane Paintless Dent Removal

Our company works on vehicles removing dents using a highly skilled trade which the metal is massaged out with special tools without disturbing the original paint, hence paintless dent removal. Besides keeping the paint and metal original its also very environmentally friendly since no paint or toxic fillers are used. Also we we are one of the most experienced companies in the business with 25 years

Target Market(s)

Retail Automobile consumers, Auto Dealerships and Auto Body Shops

Industry/Entity Type

Auto Repair

Contact Information for Business Card

Dale Hollister
PO Box 518 Brookmere, NY 11962
631-555-0148
corvanepdr@mailbox-example.com
website corvanepdr.example
youtube corvane paintless dent removal
25 years of experience removing Dents, Dings and Hail Damage

Font styles to use
Serif
Sans Serif

Colors

Designer to choose colors to be used in the design.

Requirements
Must have
• I do like things that are simple but classy and somewhat bold, also I like my logo so that should be somewhat important

```html
<!DOCTYPE html>
<html lang="en">
<head>
<meta charset="utf-8">
<title>Corvane Paintless Dent Removal – Business Card</title>
<link rel="stylesheet" href="https://fonts.googleapis.com/css2?family=Arimo:ital,wght@0,400;0,700;1,400&display=swap">
<style>
  :root {
    --backdrop: #000000;
    --card-light: #f2f2f2;
    --navy: #0f2a4f;
    --navy-deep: #07254a;
    --green: #7dc21e;
    --green-bright: #86c814;
    --text: #2b2b2b;
    --rule: #9a9a9a;
    --white: #ffffff;
  }
  * { box-sizing: border-box; margin: 0; padding: 0; }
  html, body {
    width: 1200px; height: 900px; overflow: hidden;
    background: var(--backdrop);
    font-family: "Arimo", Arial, sans-serif;
  }
  .canvas { position: relative; width: 1200px; height: 900px; }

  .card { position: absolute; top: 200px; width: 310px; height: 502px; overflow: hidden; }

  /* Front */
  .card-front {
    left: 265px;
    background: var(--card-light);
    border-radius: 52px 0 52px 0;
  }
  .brand-front {
    position: absolute; left: 0; top: 112px; width: 100%;
    text-align: center; color: var(--navy);
    font-weight: 700; font-size: 19px; line-height: 1.25; letter-spacing: 0.5px;
  }
  .holder-name {
    position: absolute; left: 26px; top: 262px;
    font-weight: 700; font-size: 18px; letter-spacing: 0.3px;
    color: var(--navy);
  }
  .holder-name .surname { color: var(--green); }
  .address {
    position: absolute; left: 28px; top: 309px;
    font-size: 15px; line-height: 19px; color: var(--text);
  }
  .contacts {
    position: absolute; left: 28px; top: 353px; list-style: none;
    font-size: 14.5px; line-height: 18.5px; color: var(--text);
  }
  .contacts li { display: flex; align-items: center; gap: 4px; }
  .contacts svg { width: 12px; height: 12px; flex: none; }
  .divider {
    position: absolute; left: 26px; top: 422px; width: 256px;
    border-top: 1px solid var(--rule);
  }
  .channel {
    position: absolute; left: 26px; top: 440px;
    display: flex; align-items: center; gap: 6px;
    font-size: 15px; color: var(--navy);
  }
  .channel-mark { width: 16px; height: 16px; background: var(--green); border-radius: 2px; }

  /* Back */
  .card-back {
    left: 641px;
    border-radius: 0 52px 0 52px;
    background: linear-gradient(135deg, var(--navy-deep) 0%, #2b6a3f 22%, var(--green-bright) 48%, #5ea81e 66%, #1e5a4a 84%, var(--navy-deep) 100%);
  }
  .swoosh { position: absolute; inset: 0; width: 100%; height: 100%; }
  .brand-back {
    position: absolute; left: 0; top: 228px; width: 100%;
    text-align: center; color: var(--white);
    font-weight: 700; font-size: 19px; line-height: 1.25; letter-spacing: 0.5px;
  }
  .tagline {
    position: absolute; left: 0; top: 424px; width: 100%;
    text-align: center; color: var(--white);
    font-style: italic; font-size: 13px; line-height: 16px; letter-spacing: 0.2px;
    text-transform: uppercase;
  }
</style>
</head>
<body>
<div class="canvas">

  <section class="card card-front">
    <p class="brand-front">CORVANE<br>PAINTLESS DENT REMOVAL</p>

    <h1 class="holder-name">DALE <span class="surname">HOLLISTER</span></h1>

    <p class="address">PO Box 518 Brookmere<br>NY 11962</p>

    <ul class="contacts">
      <li>
        <svg viewBox="0 0 12 12" aria-hidden="true"><path fill="#7dc21e" d="M1 4c0-1.5 2-3 5-3s5 1.5 5 3l-2 1-1-1.5H4L3 5zM3 6h6l1 5H2z"/></svg>
        631-555-0148
      </li>
      <li>
        <svg viewBox="0 0 12 12" aria-hidden="true"><rect x="1" y="2.5" width="10" height="7" fill="#7dc21e"/><path d="M1 2.5l5 4 5-4" fill="none" stroke="#f2f2f2" stroke-width="1"/></svg>
        corvanepdr@mailbox-example.com
      </li>
      <li>
        <svg viewBox="0 0 12 12" aria-hidden="true"><circle cx="6" cy="6" r="5" fill="#7dc21e"/><path d="M1 6h10M6 1c-2 2.5-2 7.5 0 10M6 1c2 2.5 2 7.5 0 10" fill="none" stroke="#f2f2f2" stroke-width="0.8"/></svg>
        corvanepdr.example
      </li>
    </ul>

    <div class="divider"></div>

    <p class="channel"><span class="channel-mark"></span>corvane paintless dent removal</p>
  </section>

  <section class="card card-back">
    <svg class="swoosh" viewBox="0 0 310 502" aria-hidden="true">
      <path d="M-20 470 C 60 300, 200 120, 330 60" fill="none" stroke="rgba(255,255,255,0.14)" stroke-width="26"/>
      <path d="M0 380 C 80 250, 220 120, 320 90" fill="none" stroke="rgba(255,255,255,0.12)" stroke-width="2"/>
      <path d="M300 40 C 340 120, 260 230, 180 300" fill="none" stroke="rgba(255,255,255,0.10)" stroke-width="2"/>
    </svg>
    <p class="brand-back">CORVANE<br>PAINTLESS DENT REMOVAL</p>
    <p class="tagline">25 years of experience<br>removing<br>dents, dings&nbsp; and hail damage</p>
  </section>

</div>
</body>
</html>
```